Coffee and Plastics

I am looking for a completely new site that shows the products we have. Our current site is www.velmorebrothersbeans.com. We are open minded to what designers come up with. Our current site is www.velmorebrothersbeans.com. You can you the information from there to start the site. I need these tabs on the main home page. ( Home, Coffee & Tea, Condiments, and Paper and Plastics, and Contact.) You can take photos and info from my Current site. In products page.
I will be uploading info and photo for paper and plastics.
Look and feel
Each slider illustrates characteristics of the customer's brand and the style your logo design should communicate.

```html
<!DOCTYPE html>
<html lang="en">
<head>
<meta charset="utf-8">
<title>Velmore Brothers Beans</title>
<link href="https://fonts.googleapis.com/css2?family=Mulish:wght@400;500;600&display=swap" rel="stylesheet">
<style>
:root{
  --brown:#6b4423;
  --brown-dark:#5f3f22;
  --ink:#3d3d3d;
  --muted:#777;
  --panel:#ffffff;
  --card:#f5f5f5;
  --line:#d8d8d8;
}
*{box-sizing:border-box;margin:0;padding:0}
html,body{width:1069px;height:1200px;overflow:hidden}
body{position:relative;font-family:"Mulish",sans-serif;color:var(--ink);
  background:linear-gradient(90deg,#7d7872,#a29d96 3%,#8e8983 5%,#a6a19a 95%,#7f7a74);}
.site-header{position:absolute;left:0;top:0;width:1069px;height:67px;
  background:linear-gradient(#ffffff,#ececec);border-bottom:1px solid #ddd}
.brand{position:absolute;left:66px;top:15px;font-size:29px;font-weight:500;color:var(--brown);letter-spacing:.3px}
.phone{position:absolute;right:66px;top:22px;font-size:19px;color:#8a8a8a}
.phone b{font-weight:500;color:var(--brown)}
.page{position:absolute;left:54px;top:67px;width:961px;height:1043px;background:var(--panel)}
.nav{position:absolute;right:0;top:11px;display:flex}
.nav a{display:block;padding:0 16px;height:30px;line-height:30px;font-size:13px;color:#333;text-decoration:none}
.nav a.active{background:var(--brown);color:#fff}
.slider{position:absolute;left:12px;top:49px;width:937px;height:356px;background:#eee;padding:4px}
.slider-photo{width:100%;height:100%;background:
  radial-gradient(ellipse at 50% 35%,#f08a1c 0%,#c8520c 30%,rgba(70,35,15,0) 60%),
  linear-gradient(#7a2e10,#3a1f12 60%,#2a1a10)}
.dots{position:absolute;left:50%;bottom:4px;transform:translateX(-50%);width:107px;height:33px;background:#1a1a1a;display:flex;justify-content:center;align-items:center;gap:10px}
.dots span{width:10px;height:10px;border-radius:50%;background:#9a9a9a}
.dots span.on{background:#fff}
.welcome{position:absolute;left:12px;top:420px;width:937px;text-align:center}
.welcome h1{font-size:21px;font-weight:500;color:var(--brown);margin-bottom:13px}
.welcome p{font-size:11.6px;line-height:20.5px;color:#444;padding:0 4px}
.read-more{display:inline-block;margin-top:12px;font-size:11.5px;color:#333}
.rule{position:absolute;left:12px;width:937px;height:1px;background:var(--line)}
.cards{position:absolute;left:12px;top:617px;display:flex;gap:24px}
.card{width:216px;height:214px;background:var(--card);border:1px solid #dedede;text-align:center;padding-top:11px}
.card h2{font-size:17px;font-weight:500;color:var(--brown);height:30px}
.card-photo{width:195px;height:96px;margin:0 auto;border:1px solid #ddd}
.card p{font-size:11.6px;line-height:16.5px;margin-top:15px;padding:0 12px;color:#444}
.clients{position:absolute;left:12px;top:878px;width:937px;text-align:center}
.clients h2{font-size:21px;font-weight:500;color:var(--brown)}
.client-row{position:absolute;left:0;top:51px;width:937px;height:76px}
.arrow{position:absolute;top:24px}
.client{position:absolute;top:0;height:76px;display:flex;align-items:center;justify-content:center;white-space:nowrap;font-size:13px;font-weight:600;color:var(--brown)}
.client i{display:inline-block;width:10px;height:10px;background:var(--brown);margin-right:6px;flex:none}
.site-footer{position:absolute;left:0;top:1110px;width:1069px;height:90px;background:var(--brown-dark);color:#fff}
.footer-links{position:absolute;left:66px;top:20px;font-size:11.5px}
.footer-links a{color:#fff;text-decoration:none}
.footer-links span{margin:0 6px}
.copyright{position:absolute;left:66px;top:56px;font-size:10px;color:#e6d9cc}
.connect{position:absolute;right:54px;top:34px;display:flex;align-items:center;gap:8px;font-size:12.5px}
.connect .social{width:24px;height:24px;border-radius:3px;background:#d9c6b0}
</style>
</head>
<body>
<header class="site-header">
  <div class="brand">Velmore Brothers Beans</div>
  <div class="phone">Call Us : <b>1-800-555-0142</b></div>
</header>

<main class="page">
  <nav class="nav">
    <a class="active" href="#">Home</a>
    <a href="#">Coffee &amp; Tea</a>
    <a href="#">Condiments</a>
    <a href="#">Paper</a>
    <a href="#">Plastics</a>
    <a href="#">Contact Us</a>
  </nav>

  <section class="slider">
    <div class="slider-photo" role="img" aria-label="Burlap sacks spilling roasted coffee beans against an orange glow"></div>
    <div class="dots"><span class="on"></span><span></span><span></span><span></span></div>
  </section>

  <section class="welcome">
    <h1>Welcome to Velmore Brothers Beans</h1>
    <p>We are a family-owned and operated business based in Alder Creek Texas. Since the opening of Velmore Brothers Beans plant in 1995, we have become Texas' premier independently owned coffee packaging company. Our success relies solely on the principle of selling only the freshest, highest-quality in-room coffee available. Velmore Brothers packages and supplies in-room coffee, tea products, and condiments. Whether we're supplying a 50-room Hotel or a 500-room grand resort, we have the distribution capacity to fill your rooms with the most aromatic and robust coffees and teas available at competitive prices.</p>
    <span class="read-more">&lsaquo;&lsaquo; READ MORE &nbsp;&rsaquo;&rsaquo;</span>
  </section>

  <div class="rule" style="top:594px"></div>

  <section class="cards">
    <article class="card">
      <h2>Coffee &amp; Tea</h2>
      <div class="card-photo" role="img" aria-label="Cup of tea on a bed of coffee beans" style="background:radial-gradient(ellipse at 50% 55%,#5a3422 0%,#3b2216 45%,#fff 62%)"></div>
      <p>Sed ut perspiciatis unde omnis iste natus error sit voluptatem accusantium..</p>
    </article>
    <article class="card">
      <h2>Condiments</h2>
      <div class="card-photo" role="img" aria-label="Spoons of sauces and condiments on a wooden table" style="background:linear-gradient(135deg,#7a4a2c,#a9694a 40%,#d9b36a 70%,#6b3d24)"></div>
      <p>Sed ut perspiciatis unde omnis iste natus error sit voluptatem accusantium..</p>
    </article>
    <article class="card">
      <h2>Paper</h2>
      <div class="card-photo" role="img" aria-label="Stack of kraft paper cups with a lid" style="background:linear-gradient(#f1f1f1 60%,#8b8480)"></div>
      <p>Sed ut perspiciatis unde omnis iste natus error sit voluptatem accusantium..</p>
    </article>
    <article class="card">
      <h2>Plastics</h2>
      <div class="card-photo" role="img" aria-label="White plastic compartment food trays" style="background:radial-gradient(ellipse at 50% 50%,#e8e8e8 0%,#cfcfcf 50%,#2e2e33 80%)"></div>
      <p>Sed ut perspiciatis unde omnis iste natus error sit voluptatem accusantium..</p>
    </article>
  </section>

  <div class="rule" style="top:857px"></div>

  <section class="clients">
    <h2>Serving Fine Establishments Everywhere!</h2>
    <div class="client-row">
      <svg class="arrow" style="left:0" width="14" height="24" viewBox="0 0 14 24"><path d="M12 2 2 12l10 10" fill="none" stroke="#444" stroke-width="1.6"/></svg>
      <div class="client" style="left:42px;width:130px"><i></i>Oakridge Stay</div>
      <div class="client" style="left:190px;width:130px"><i></i>Larkspur Lodge</div>
      <div class="client" style="left:338px;width:138px"><i></i>Millbrook Hotel</div>
      <div class="client" style="left:490px;width:134px"><i></i>Tidewater House</div>
      <div class="client" style="left:636px;width:140px"><i></i>Cedar Point Rooms</div>
      <div class="client" style="left:780px;width:132px"><i></i>Blue Mesa Resort</div>
      <svg class="arrow" style="right:0" width="14" height="24" viewBox="0 0 14 24"><path d="M2 2l10 10L2 22" fill="none" stroke="#444" stroke-width="1.6"/></svg>
    </div>
  </section>
</main>

<footer class="site-footer">
  <div class="footer-links">
    <a href="#">Home</a><span>/</span><a href="#">Coffee &amp; Tea</a><span>/</span><a href="#">Condiments</a><span>/</span><a href="#">Paper</a><span>/</span><a href="#">Plastics</a><span>/</span><a href="#">Contact Us</a>
  </div>
  <div class="copyright">Copyright © 2014. Velmore Brothers Beans. All Right Reserved</div>
  <div class="connect">Connect Us: <span class="social" aria-label="Social link"></span><span class="social" aria-label="Social link"></span></div>
</footer>
</body>
</html>
```